Customer Facing Document Design

Looking for professional design in Word for 5 Templates:

- Purchase Contract
- Sales Contract
- Packing List
- Settlement Report
- Invoice

I have attached our current designs and also some example designs that we want to look similar to. We want our company logo included on all documents. On the Purchase Order, Sales Order, Settlement Report, Invoice we also want our ISO accreditation picture and KRBA logo included.

```html
<!DOCTYPE html>
<html lang="en">
<head>
<meta charset="utf-8">
<title>Corvane Customer Documents</title>
<link href="https://fonts.googleapis.com/css2?family=Open+Sans:wght@400;600;700&family=Roboto:wght@400;700&display=swap" rel="stylesheet">
<style>
:root{
  --backdrop:#232323;
  --paper:#ffffff;
  --head-bg:#f3f3f3;
  --ink:#1e1e1e;
  --soft-ink:#444;
  --rule:#8d8d8d;
  --band:#a1a1a7;
  --pill:#222;
  --brand-grey:#8c8c8c;
  --cert-grey:#d4d4d4;
}
*{box-sizing:border-box;margin:0;padding:0}
html,body{width:1200px;height:2177px;overflow:hidden;background:var(--backdrop)}
.sheet{width:1420px;height:2576px;transform:scale(0.84507);transform-origin:0 0;position:relative;font-family:"Open Sans",sans-serif;color:var(--ink)}
.page{position:absolute;width:612px;height:792px;background:var(--paper);overflow:hidden}
.p1{left:86px;top:77px}.p2{left:729px;top:77px}.p3{left:86px;top:902px}.p4{left:729px;top:902px}.p5{left:408px;top:1727px}
.abs{position:absolute}
.page-head{position:absolute;left:0;top:0;width:612px;height:92px;background:var(--head-bg);border-bottom:1px solid var(--rule)}
.page-head::after{content:"";position:absolute;left:295px;top:92px;border-left:5px solid transparent;border-right:5px solid transparent;border-top:7px solid #777}
.brand{position:absolute;left:24px;top:18px;display:flex;align-items:center;gap:6px}
.brand-dot{width:54px;height:54px;border-radius:50%;background:#c9c9c9}
.brand-name{font-family:"Roboto",sans-serif;font-weight:700;font-size:22px;color:var(--brand-grey);letter-spacing:.5px}
.co-pill{position:absolute;left:211px;top:17px;width:191px;height:15px;border-radius:8px;background:var(--pill);color:#fff;font-family:"Roboto",sans-serif;font-weight:700;font-size:9.5px;line-height:15px;text-align:center}
.co-addr{position:absolute;left:160px;width:293px;top:43px;text-align:center;font-family:"Roboto",sans-serif;font-size:9.5px;line-height:13px;color:var(--ink);white-space:nowrap}
.co-addr b{font-weight:700}
.cert-area{position:absolute;left:448px;top:30px;width:70px;height:30px;background:var(--cert-grey)}
.member-name{position:absolute;left:530px;top:35px;font-family:"Roboto",sans-serif;font-weight:700;font-size:14px;color:#555}
.doc-title{position:absolute;left:0;width:612px;top:126px;text-align:center;font-weight:700;font-size:20px;letter-spacing:.3px}
.rule{position:absolute;left:48px;width:516px;height:1px;background:var(--rule)}
.vrule{position:absolute;width:1px;background:var(--rule)}
.block-label{font-weight:700;font-size:10px}
.small{font-size:8px;line-height:13px;color:var(--soft-ink)}
.meta{position:absolute;left:350px;font-size:7.6px;line-height:13px}
.meta dt{position:absolute;left:0;font-weight:700}
.meta dd{margin-left:92px;color:var(--soft-ink)}
.grid{position:absolute;left:48px;border-collapse:collapse;table-layout:fixed;font-size:7.8px}
.grid th{background:var(--band);font-size:9.5px;font-weight:600;text-align:left;padding:0 6px;height:21px;color:#222;border-left:1px solid #fff;white-space:nowrap;overflow:hidden}
.grid th:first-child{border-left:none}
.grid td{padding:0 6px;border-left:1px solid #bbb;border-bottom:1px solid #bbb;color:var(--soft-ink);vertical-align:middle;white-space:nowrap;overflow:hidden}
.grid td.wrap{white-space:normal}
.grid td:first-child{border-left:none}
.grid .tot td{font-weight:700;color:var(--ink);font-size:10px;border-bottom:1px solid var(--rule)}
.grid.tight th{font-size:8.6px;padding:0 4px}
.grid.tight td{padding:0 4px}
.conds{position:absolute;left:61px;top:417px}
.conds h4{font-size:10px;font-weight:700;margin-bottom:14px}
.conds li{list-style:none;font-size:7.6px;line-height:14px;color:var(--soft-ink)}
.box{position:absolute;border:1.5px solid #666}
.box .block-label{margin-bottom:2px}
</style>
</head>
<body>
<div class="sheet">

<section class="page p1">
  <header class="page-head">
    <div class="brand"><div class="brand-dot"></div><span class="brand-name">CORVANE</span></div>
    <div class="co-pill">CORVANE ALLOYS &amp; METALS, LLC</div>
    <div class="co-addr">4180 Marlow Circle, Fenwick Park. CA 90711<br><b>W:</b> www.corvane-am.com</div>
    <div class="cert-area" role="img" aria-label="Certification badge"></div><span class="member-name">KRBA</span>
  </header>
  <h1 class="doc-title">PURCHASE ORDER</h1>
  <div class="rule" style="top:161px"></div>
  <div class="vrule" style="left:306px;top:161px;height:110px"></div>
  <div class="abs" style="left:61px;top:178px"><div class="block-label">Vendor</div><div class="small">Brisco Alloys, LP<br>2214 Tanner Street<br>Houston</div></div>
  <dl class="meta" style="top:171px">
    <dt>P.O. Number:</dt><dd>BRISCO 060525</dd>
    <dt>P.O. Issue Date:</dt><dd>May 6, 2025</dd>
    <dt>Deliver by:</dt><dd>June 2025</dd>
    <dt>Payment Terms:</dt><dd>30 Days from date of receipt<br>at Corvane</dd>
    <dt>F.O.B:</dt><dd>CPT Carriage paid to CORVANE!</dd>
  </dl>
  <div class="rule" style="top:271px"></div>
  <table class="grid" style="top:296px;width:516px">
    <colgroup><col style="width:40px"><col style="width:76px"><col style="width:216px"><col style="width:54px"><col style="width:42px"><col style="width:88px"></colgroup>
    <tr><th>Item</th><th>Alloy</th><th>Description</th><th>Lbs</th><th>$/Lb</th><th>Total</th></tr>
    <tr style="height:33px"><td>1</td><td>Alloy 939 Low Zr</td><td class="wrap">Solids suitable for sorting &amp; prep to vac<br>Qty - 15,000 to 20,000 Lbs</td><td>20,000</td><td>$5.50</td><td>$110,000.00</td></tr>
    <tr class="tot" style="height:40px"><td colspan="3" style="text-align:right;padding-right:8px">Total:</td><td colspan="3" style="text-align:right;padding-right:12px">$110,000.00</td></tr>
  </table>
  <div class="conds"><h4>Conditions:</h4><ul>
    <li>1. No coatings, inserts, or attachments</li>
    <li>2. Any material with inserts / attachments, payable weight is yielded recovered.</li>
    <li>3. Any material with Zr TVC, price reduction by US$1.75/lb or Buyer’s right of rejection</li>
    <li>4. Alloyed Zr max 0.022 as per chems provided, all other elements nominal</li></ul></div>
  <div class="box" style="left:48px;top:669px;width:356px;height:90px">
    <div class="vrule" style="left:166px;top:0;height:88px;background:#666"></div>
    <div class="abs" style="left:12px;top:9px"><div class="block-label">Ship to:</div><div class="small" style="line-height:14px">CORVANE A&amp;M<br>4180 MARLOW CIRCLE<br>FENWICK PARK<br>CA 90711</div></div>
    <div class="abs block-label" style="left:191px;top:10px">Signed:</div>
  </div>
</section>

<section class="page p2">
  <header class="page-head">
    <div class="brand"><div class="brand-dot"></div><span class="brand-name">CORVANE</span></div>
    <div class="co-pill">CORVANE ALLOYS &amp; METALS, LLC</div>
    <div class="co-addr">4180 Marlow Circle, Fenwick Park. CA 90711<br><b>W:</b> www.corvane-am.com</div>
    <div class="cert-area" role="img" aria-label="Certification badge"></div><span class="member-name">KRBA</span>
  </header>
  <h1 class="doc-title">SALES ORDER</h1>
  <div class="rule" style="top:161px"></div>
  <div class="vrule" style="left:306px;top:161px;height:110px"></div>
  <div class="abs" style="left:61px;top:178px"><div class="block-label">Customer:</div><div class="small" style="line-height:14px">CORVANE A&amp;M<br>4180 MARLOW CIRCLE<br>FENWICK PARK<br>CA 90711</div></div>
  <dl class="meta" style="top:171px">
    <dt>S.O. Number:</dt><dd>Keystone 092325</dd>
    <dt>S.O. Issue Date:</dt><dd>September 23, 2025</dd>
    <dt>Deliver by:</dt><dd>September 2025</dd>
    <dt>Payment Terms:</dt><dd>Net 30</dd>
    <dt>F.O.B:</dt><dd>DDP Ardmoor</dd>
    <dt>Buyer’s PO:</dt><dd style="font-weight:700;color:var(--ink)">8554</dd>
  </dl>
  <div class="rule" style="top:271px"></div>
  <table class="grid" style="top:296px;width:516px">
    <colgroup><col style="width:40px"><col style="width:94px"><col style="width:198px"><col style="width:54px"><col style="width:42px"><col style="width:88px"></colgroup>
    <tr><th>Item</th><th>Alloy</th><th>Description</th><th>Lbs</th><th>$/Lb</th><th>Total</th></tr>
    <tr style="height:33px"><td>1</td><td>NXS-2 VQ Solids</td><td class="wrap">Solids suitable for sorting &amp; prep to vac<br>Qty - 15,000 to 20,000 Lbs</td><td>1,000</td><td>$8.75</td><td>$8,750.00</td></tr>
    <tr class="tot" style="height:40px"><td colspan="3" style="text-align:right;padding-right:8px">Total:</td><td colspan="3" style="text-align:right;padding-right:12px">$8,750.00</td></tr>
  </table>
  <div class="conds"><h4>Conditions:</h4><ul>
    <li>1. No coatings, inserts, or attachments</li>
    <li>2. Any material with inserts / attachments, payable weight is yielded recovered.</li>
    <li>3. Any material with Zr TVC, price reduction by US$1.75/lb or Buyer’s right of rejection</li>
    <li>4. Alloyed Zr max 0.022 as per chems provided, all other elements nominal</li></ul></div>
  <div class="box" style="left:48px;top:669px;width:356px;height:90px">
    <div class="vrule" style="left:166px;top:0;height:88px;background:#666"></div>
    <div class="abs" style="left:12px;top:9px"><div class="block-label">Ship to:</div><div class="small" style="line-height:14px">KEYSTONE ALLOYS, LLC<br>880 ROUTE 14<br>ARDMOOR<br>IL 61090</div></div>
    <div class="abs block-label" style="left:191px;top:10px">Signed:</div>
  </div>
</section>

<section class="page p3">
  <header class="page-head">
    <div class="brand"><div class="brand-dot"></div><span class="brand-name">CORVANE</span></div>
    <div class="co-pill">CORVANE ALLOYS &amp; METALS, LLC</div>
    <div class="co-addr">4180 Marlow Circle, Fenwick Park. CA 90711<br><b>W:</b> www.corvane-am.com</div>
    <div class="cert-area" role="img" aria-label="Certification badge"></div><span class="member-name">KRBA</span>
  </header>
  <h1 class="doc-title">PACKING LIST PEAK TP2</h1>
  <div class="rule" style="top:161px"></div>
  <div class="vrule" style="left:306px;top:161px;height:69px"></div>
  <div class="abs" style="left:58px;top:167px"><div class="block-label">Customer:</div><div class="small" style="line-height:10px">CORVANE A&amp;M<br>4180 MARLOW CIRCLE<br>FENWICK PARK<br>CA 90711</div></div>
  <dl class="meta" style="top:165px;left:324px">
    <dt>Despatched:</dt><dd style="margin-left:99px">September 19, 2025</dd>
    <dt>Sales Order:</dt><dd style="margin-left:99px">000000</dd>
    <dt>Packing List No.:</dt><dd style="margin-left:99px">000</dd>
    <dt>Container:</dt><dd style="margin-left:99px">Destination</dd>
  </dl>
  <div class="rule" style="top:230px"></div>
  <table class="grid" style="top:256px;width:516px;font-size:7.4px">
    <colgroup><col style="width:40px"><col style="width:70px"><col style="width:92px"><col style="width:107px"><col style="width:71px"><col style="width:65px"><col style="width:71px"></colgroup>
    <tr><th>Item</th><th>BOX</th><th>Material</th><th>Packages</th><th>Gross (lbs.)</th><th>Tare (lbs.)</th><th>Net (lbs.)</th></tr>
    <tr style="height:9px"><td></td><td></td><td></td><td></td><td></td><td></td><td></td></tr>
    <tr style="height:15px"><td>1</td><td>031925/03</td><td>Alloy 718 Turnings</td><td>bag inside stillage</td><td>303</td><td>50</td><td>253</td></tr>
    <tr style="height:15px"><td>2</td><td>031925/04</td><td>Alloy 718 Turnings</td><td>stillage</td><td>461</td><td>55</td><td>406</td></tr>
    <tr style="height:15px"><td>3</td><td>031925/05</td><td>Alloy 718 Turnings</td><td>stillage</td><td>242</td><td>51</td><td>191</td></tr>
    <tr style="height:15px"><td>4</td><td>31925/06</td><td>Alloy 718 Turnings</td><td>stillage</td><td>769</td><td>54</td><td>715</td></tr>
    <tr style="height:15px"><td>5</td><td>031925/07</td><td>Alloy 718 Turnings</td><td>stillage</td><td>281</td><td>45</td><td>236</td></tr>
    <tr style="height:15px"><td>6</td><td>031925/08</td><td>Alloy 718 Turnings</td><td>stillage</td><td>473</td><td>49</td><td>424</td></tr>
    <tr style="height:15px"><td>7</td><td>031925/09</td><td>Alloy 718 Turnings</td><td>stillage</td><td>698</td><td>52</td><td>646</td></tr>
    <tr style="height:15px"><td>8</td><td>031925/10</td><td>Alloy 718 Turnings</td><td>stillage</td><td>202</td><td>51</td><td>151</td></tr>
    <tr style="height:15px"><td>9</td><td>031925/11</td><td>Alloy 718 Turnings</td><td>stillage</td><td>682</td><td>52</td><td>630</td></tr>
    <tr style="height:15px"><td>10</td><td>031925/12</td><td>Alloy 718 Turnings</td><td>stillage</td><td>764</td><td>51</td><td>713</td></tr>
    <tr style="height:15px"><td>11</td><td>031925/13</td><td>Alloy 718 Turnings</td><td>stillage</td><td>281</td><td>45</td><td>236</td></tr>
    <tr style="height:15px"><td>12</td><td>031925/14</td><td>Alloy 718 Turnings</td><td>bag inside stillage</td><td>144</td><td>10</td><td>134</td></tr>
    <tr style="height:15px"><td>13</td><td>031925/15</td><td>Alloy 718 Turnings</td><td>stillage</td><td>301</td><td>52</td><td>249</td></tr>
    <tr style="height:15px"><td>14</td><td>031925/16</td><td>Alloy 718 Turnings</td><td>stillage</td><td>228</td><td>50</td><td>178</td></tr>
    <tr style="height:15px"><td>15</td><td>031925/17</td><td>Alloy 718 Turnings</td><td>stillage</td><td>225</td><td>50</td><td>175</td></tr>
    <tr style="height:15px"><td>16</td><td>031925/18</td><td>Alloy 718 Turnings</td><td>stillage</td><td>673</td><td>44</td><td>629</td></tr>
    <tr style="height:15px"><td>17</td><td>031925/19</td><td>Alloy 718 Turnings</td><td>stillage</td><td>102</td><td>46</td><td>56</td></tr>
    <tr style="height:15px"><td>18</td><td>031925/20</td><td>Alloy 718 Turnings</td><td>drum</td><td>67</td><td>14</td><td>53</td></tr>
    <tr style="height:15px"><td>19</td><td>031925/21</td><td>Alloy 718 Turnings</td><td>bag inside metal box</td><td>545</td><td>132</td><td>413</td></tr>
    <tr style="height:15px"><td>20</td><td>031925/22</td><td>Alloy 718 Turnings</td><td>bag</td><td>77</td><td>25</td><td>52</td></tr>
    <tr style="height:15px"><td>21</td><td>21031925/23</td><td>Alloy 625 Turnings</td><td>drum</td><td>66</td><td>10</td><td>56</td></tr>
    <tr style="height:15px"><td>22</td><td>031925/24</td><td>Alloy 625 Turnings</td><td>bag</td><td>140</td><td>2</td><td>138</td></tr>
    <tr class="tot" style="height:34px"><td></td><td></td><td></td><td>Grand Total</td><td>7,724</td><td>990</td><td>6,734</td></tr>
  </table>
  <div class="box" style="left:48px;top:679px;width:230px;height:84px">
    <div class="vrule" style="left:119px;top:0;height:82px;background:#666"></div>
    <div class="abs" style="left:12px;top:9px"><div class="block-label">Ship to:</div><div class="small" style="line-height:12px">KEYSTONE ALLOYS, LLC<br>880 ROUTE 14<br>ARDMOOR<br>IL 61090</div></div>
    <div class="abs block-label" style="left:134px;top:10px">Signed:</div>
  </div>
  <div class="box" style="left:289px;top:679px;width:248px;height:84px">
    <div class="abs" style="left:13px;top:11px;font-size:8.4px;line-height:13px;font-weight:700">Driver Name:<br>Date:<br>Vehicle Registration:<br>Signature:</div>
    <div class="abs" style="left:112px;top:11px;font-size:8.4px;line-height:13px;color:var(--soft-ink)">Name Here<br>00/00/2025<br>000</div>
  </div>
  <div class="abs" style="left:552px;top:752px;font-size:7.5px;color:var(--soft-ink)">01</div>
</section>

<section class="page p4">
  <header class="page-head">
    <div class="brand"><div class="brand-dot"></div><span class="brand-name">CORVANE</span></div>
    <div class="co-pill">CORVANE ALLOYS &amp; METALS, LLC</div>
    <div class="co-addr" style="left:140px;width:333px">4180 Marlow Circle, Fenwick Park. CA 90711<br><b>W:</b> www.corvane-am.com &nbsp;| &nbsp;<b>E:</b> OWEN@CORVANE-AM.COM<br><b>T: +44 7000 118240</b></div>
    <div class="cert-area" role="img" aria-label="Certification badge"></div><span class="member-name">KRBA</span>
  </header>
  <h1 class="doc-title">SETTLEMENT REPORT</h1>
  <div class="rule" style="top:161px"></div>
  <div class="vrule" style="left:306px;top:161px;height:110px"></div>
  <dl class="meta" style="left:61px;top:171px">
    <dt>SUPPLIER:</dt><dd>NORTHGATE RECYCLING</dd>
    <dt>Lot No:</dt><dd>877</dd>
    <dt>PO No.:</dt><dd>&nbsp;</dd>
  </dl>
  <dl class="meta" style="top:171px">
    <dt>DATE:</dt><dd>September 19, 2025</dd>
    <dt>RECEIVING DATE:</dt><dd>August 11, 2025</dd>
  </dl>
  <div class="rule" style="top:271px"></div>
  <table class="grid tight" style="top:296px;width:516px;font-size:7.2px">
    <colgroup><col style="width:34px"><col style="width:64px"><col style="width:120px"><col style="width:62px"><col style="width:62px"><col style="width:38px"><col style="width:56px"></colgroup>
    <tr><th>Item</th><th>Advised As:</th><th>Graded As:</th><th>Advised (Lbs)</th><th>Received (Lbs)</th><th>$ / LB</th><th>Total $</th></tr>
    <tr style="height:6px"><td></td><td></td><td></td><td></td><td></td><td></td><td></td></tr>
    <tr style="height:15px"><td>1</td><td>Alloy 718 Turnings</td><td>Alloy 718 Turnings - 1% Alum 1% Fe</td><td></td><td>284</td><td>$5.2000</td><td>$1,476.80</td></tr>
    <tr style="height:15px"><td></td><td></td><td>Alloy 718 Turnings - 1% Alum 1% Fe</td><td></td><td>1382</td><td>$5.2000</td><td>$7,186.40</td></tr>
    <tr style="height:15px"><td></td><td></td><td>Alloy 718 Turnings - 1% Alum 1% Fe</td><td></td><td>1390</td><td>$5.2000</td><td>$7,228.00</td></tr>
    <tr style="height:15px"><td></td><td></td><td>Steel Turnings</td><td></td><td>556</td><td>$0.0000</td><td>$0.00</td></tr>
    <tr style="height:15px"><td></td><td></td><td>Alloy 718 Turnings - 1% Alum 1% Fe</td><td></td><td>1340</td><td>$5.2000</td><td>$6,968.00</td></tr>
    <tr style="height:15px"><td></td><td></td><td>Alloy 718 Turnings - 1% Alum 1% Fe</td><td></td><td>1528</td><td>$5.2000</td><td>$7,945.60</td></tr>
    <tr class="tot" style="height:36px"><td></td><td></td><td></td><td style="font-size:8.5px">0</td><td style="font-size:8.5px">6,480</td><td style="font-size:8.5px">Total</td><td style="font-size:8.5px">$30,804.80</td></tr>
  </table>
  <p class="abs small" style="left:61px;top:492px;width:450px;font-size:7.6px;line-height:14px">We are pleased to enclose our Settlement Report for your recent delivery. Should you have any questions or concerns, please do not hesitate to contact us.</p>
</section>

<section class="page p5">
  <header class="page-head">
    <div class="brand"><div class="brand-dot"></div><span class="brand-name">CORVANE</span></div>
    <div class="co-pill">CORVANE ALLOYS &amp; METALS, LLC</div>
    <div class="co-addr">4180 Marlow Circle, Fenwick Park. CA 90711<br><b>W:</b> www.corvane-am.com</div>
    <div class="cert-area" role="img" aria-label="Certification badge"></div><span class="member-name">KRBA</span>
  </header>
  <h1 class="doc-title">SALES INVOICE</h1>
  <div class="rule" style="top:161px"></div>
  <div class="vrule" style="left:306px;top:161px;height:110px"></div>
  <div class="abs" style="left:61px;top:172px"><div class="block-label">Customer:</div><div class="small" style="line-height:13px">Meridian Metal Services<br>4420 Larkin Ave<br>Cleveland<br>OH 44120</div></div>
  <dl class="meta" style="top:171px">
    <dt>Contract No:</dt><dd>Meridian 050725</dd>
    <dt>Date:</dt><dd>September 22, 2025</dd>
    <dt>Order No:</dt><dd>P.O. 13222</dd>
    <dt>Delivery:</dt><dd>September 22, 2025</dd>
    <dt>Payment:</dt><dd>On receipt of invoice</dd>
    <dt>Due Date:</dt><dd>September 22, 2025</dd>
  </dl>
  <div class="rule" style="top:271px"></div>
  <table class="grid" style="top:296px;width:516px">
    <colgroup><col style="width:40px"><col style="width:292px"><col style="width:74px"><col style="width:42px"><col style="width:68px"></colgroup>
    <tr><th>Item</th><th>Material</th><th>Lbs weight</th><th>$/Lb</th><th>$ Total</th></tr>
    <tr style="height:33px"><td>1</td><td>Settlement balance shortage agreed by Owen Hartley/Paul Reyes</td><td>2,000</td><td>$1.00</td><td>$2,000.00</td></tr>
    <tr class="tot" style="height:32px"><td colspan="2" style="text-align:right;padding-right:6px">Total:</td><td>2,000</td><td></td><td>$2,000.00</td></tr>
  </table>
  <div class="box" style="left:48px;top:669px;width:356px;height:90px">
    <div class="vrule" style="left:182px;top:0;height:88px;background:#666"></div>
    <div class="abs" style="left:12px;top:9px"><div class="block-label">REMIT TO:</div><div class="small" style="line-height:14px">Payment by ACH<br>Routing Number: 410 377 205<br>Account Number: 027 845 3319<br>Bank: Harbor State Bank</div></div>
    <div class="abs block-label" style="left:191px;top:10px">Signed:</div>
  </div>
</section>

</div>
</body>
</html>
```